SirKettle needs a new packaging

We are Coffee Roasters based in Versailles France.

We want a new design for our coffee packaging. The packaging is a basic brown paper bag. We are sticking on it a 99.1mm x 67.7mm Label.

We want a new design for the label. The label should have the following info : Name of the coffee, origin, one line of description, our website www.sirkettle.fr.

Enclosed you will find our logo, as well as a picture of our current packaging

The Design should be "simple yet sophisticate".

```html
<!DOCTYPE html>
<html lang="fr">
<head>
<meta charset="utf-8">
<title>SirKettle – Nº5 coffee label</title>
<link href="https://fonts.googleapis.com/css2?family=Libre+Baskerville:ital,wght@0,400;0,700;1,400&family=Questrial&display=swap" rel="stylesheet">
<style>
  :root {
    --ink: #2b2828;
    --paper: #ffffff;
    --bean-pattern: #f1f1f1;
    --frame: #2b2828;
  }
  html, body {
    margin: 0;
    padding: 0;
    width: 1200px;
    height: 820px;
    overflow: hidden;
    background: var(--paper);
  }
  .label {
    position: relative;
    width: 1200px;
    height: 820px;
    background: var(--paper);
    color: var(--ink);
    font-family: "Libre Baskerville", "Century Schoolbook", serif;
  }
  .label__pattern {
    position: absolute;
    inset: 12px;
    background: var(--bean-pattern);
  }
  .label__border {
    position: absolute;
    inset: 0;
  }
  .brand {
    position: absolute;
    left: 268px;
    top: 95px;
    width: 660px;
    height: 190px;
  }
  .brand__dot {
    position: absolute;
    left: 10px;
    top: 40px;
    width: 100px;
    height: 100px;
    border-radius: 50%;
    background: var(--ink);
  }
  .brand__name {
    position: absolute;
    left: 156px;
    top: 33px;
    margin: 0;
    font-weight: 700;
    font-size: 88px;
    line-height: 1;
    letter-spacing: -1px;
    white-space: nowrap;
  }
  .brand__tagline {
    position: absolute;
    left: 162px;
    top: 139px;
    margin: 0;
    font-family: "Questrial", "Century Gothic", sans-serif;
    font-size: 27px;
    line-height: 1;
    white-space: nowrap;
  }
  .line {
    position: absolute;
    left: 0;
    width: 1200px;
    margin: 0;
    text-align: center;
    line-height: 1;
    white-space: nowrap;
  }
  .coffee-name {
    top: 337px;
    font-size: 84px;
    font-weight: 700;
  }
  .coffee-name sup {
    font-size: 0.45em;
    vertical-align: 0.95em;
    margin-left: 2px;
  }
  .coffee-blend {
    top: 432px;
    font-size: 30px;
    font-weight: 700;
  }
  .coffee-origin {
    top: 483px;
    font-size: 30px;
    font-weight: 700;
  }
  .coffee-description {
    top: 552px;
    font-size: 24px;
    font-style: italic;
    font-weight: 400;
  }
  .website {
    top: 635px;
    font-size: 72px;
    font-weight: 700;
  }
</style>
</head>
<body>
  <div class="label">
    <div class="label__pattern" role="img" aria-label="Faint repeating pattern of outlined coffee beans"></div>

    <svg class="label__border" width="1200" height="820" viewBox="0 0 1200 820" aria-hidden="true">
      <rect x="6" y="6" width="1188" height="808" fill="none" stroke="var(--frame)" stroke-width="12"/>
      <rect x="6" y="6" width="1188" height="808" fill="none" stroke="#ffffff" stroke-width="2.6" stroke-linecap="round" stroke-dasharray="0 5.5"/>
      <rect x="42" y="40" width="1116" height="740" fill="none" stroke="var(--frame)" stroke-width="2.6"/>
    </svg>

    <header class="brand">
      <span class="brand__dot" aria-hidden="true"></span>
      <p class="brand__name">SirKettle</p>
      <p class="brand__tagline">Artisan Torréfacteur</p>
    </header>

    <h1 class="line coffee-name">N<sup>o</sup>5 de SirKettle</h1>
    <p class="line coffee-blend">100% Arabica</p>
    <p class="line coffee-origin">(Bresil, Congo, Ethipie)</p>
    <p class="line coffee-description">One line text goes here, lorem ipsum doler amit</p>
    <p class="line website">www.sirkettle.fr</p>
  </div>
</body>
</html>
```